Book cover for book about Climate Change

Looking for a clean, bold, and attractive cover for a mass-market paperback (5.5"x 8.5") about solving the climate change problem. Title is either "Where the Rivers Meet” or A Harbor Made of Glass” (your choice), subtitle is "A practical field guide to mending the weather — so that the young ones after us inherit steady seasons and open skies," author is Lorne Whitcombe. Thinking that it *might* feature an image of Earth (or a portion thereof) and its very thin layer of atmosphere -- but STRONGLY encourage other ideas too!

Requirements
Nice to have
• Keep it positive — NOT scary doom-and-gloom

```html
<!DOCTYPE html>
<html lang="en">
<head>
<meta charset="utf-8">
<title>A Harbor Made of Glass — Lorne Whitcombe</title>
<link rel="stylesheet" href="https://fonts.googleapis.com/css2?family=Oswald:wght@600&family=Poppins:wght@500&display=swap">
<style>
  :root {
    --page-bg: #e4e4e4;
    --sky-teal: #34504e;
    --sky-deep: #1b2c31;
    --halo-warm: #d8b59c;
    --halo-orange: #c8683a;
    --earth-ocean: #2c3f6e;
    --earth-cloud: #e8ecef;
    --earth-land: #b88a5a;
    --band-blue: rgba(10, 40, 130, 0.72);
    --type-white: #ffffff;
  }
  * { margin: 0; padding: 0; box-sizing: border-box; }
  html, body { width: 1200px; height: 1200px; overflow: hidden; }
  body { background: var(--page-bg); position: relative; }

  .cover {
    position: absolute;
    left: 182px; top: 29px;
    width: 835px; height: 1141px;
    overflow: hidden;
    box-shadow: 0 2px 8px rgba(0,0,0,0.18);
  }
  .cover__photo {
    position: absolute; inset: 0;
    background:
      radial-gradient(ellipse 58% 62% at 50% 58%,
        var(--halo-warm) 0%,
        #c4a590 52%,
        rgba(200,104,58,0.75) 66%,
        rgba(52,80,78,0.9) 76%,
        var(--sky-teal) 86%,
        var(--sky-deep) 100%);
  }
  .cover__earth {
    position: absolute;
    left: 212px; top: 227px;
    width: 450px; height: 450px;
    border-radius: 50%;
    background:
      radial-gradient(circle at 40% 72%, var(--earth-cloud) 0%, rgba(232,236,239,0.5) 25%, rgba(232,236,239,0) 45%),
      radial-gradient(circle at 35% 18%, var(--earth-land) 0%, rgba(184,138,90,0.6) 20%, rgba(184,138,90,0) 40%),
      radial-gradient(circle at 50% 50%, #4a5d8a 0%, var(--earth-ocean) 70%, #1d2a4e 100%);
    box-shadow: 0 0 40px rgba(0,0,0,0.35);
  }
  .cover__title {
    position: absolute;
    left: 0; right: 0; top: 44px;
    text-align: center;
    font-family: "Oswald", sans-serif;
    font-weight: 600;
    color: var(--type-white);
    text-transform: uppercase;
    line-height: 1;
  }
  .cover__title-main { display: block; font-size: 120px; letter-spacing: 1px; }
  .cover__title-sub { display: block; font-size: 68px; margin-top: 4px; letter-spacing: 4px; }

  .cover__band {
    position: absolute;
    left: 0; right: 0; top: 758px; height: 162px;
    background: var(--band-blue);
    display: flex; align-items: center; justify-content: center;
  }
  .cover__subtitle {
    font-family: "Poppins", sans-serif;
    font-weight: 500;
    font-size: 21px;
    line-height: 36px;
    color: var(--type-white);
    text-align: center;
    text-transform: uppercase;
  }
  .cover__author {
    position: absolute;
    left: 0; right: 0; top: 950px;
    text-align: center;
    font-family: "Oswald", sans-serif;
    font-weight: 600;
    font-size: 72px;
    line-height: 1;
    color: var(--type-white);
    text-transform: uppercase;
  }
</style>
</head>
<body>
  <main class="cover">
    <div class="cover__photo" role="img" aria-label="Photograph of a hazy teal sky with a warm glowing halo and an open hand silhouetted below, reaching up"></div>
    <div class="cover__earth" role="img" aria-label="Photograph of planet Earth seen from space, with clouds over ocean and land"></div>

    <h1 class="cover__title">
      <span class="cover__title-main">A Harbor</span>
      <span class="cover__title-sub">Made of Glass</span>
    </h1>

    <div class="cover__band">
      <p class="cover__subtitle">
        A practical field guide to mending the weather<br>
        so that the young ones after us inherit<br>
        steady seasons and open skies
      </p>
    </div>

    <p class="cover__author">Lorne Whitcombe</p>
  </main>
</body>
</html>
```